PlumVesta screens tidy up

We would like advice on how to better present the following home page and overview pages.

The existing website is functional, but the pages don't appear professionals and pleasing to the eye. We would specifically like feedback on alignment and padding of icons and text to make the screen more appealing and polished.

We are following the quartzline design system.

1 page

Sans Serif
• IBM Plex, Poppins

```html
<!DOCTYPE html>
<html lang="en">
<head>
<meta charset="utf-8">
<title>PlumVesta screens</title>
<link href="https://fonts.googleapis.com/css2?family=Poppins:wght@400;500;600&display=swap" rel="stylesheet">
<style>
:root{
  --backdrop:#7a7a7a;
  --orange:#f39834;
  --sidebar:#120d0b;
  --sidebar-band:#2e2a28;
  --sidebar-active:#3b3634;
  --canvas:#f6f6f6;
  --card:#ffffff;
  --ink:#111111;
  --muted:#333333;
  --line:#e2e2e2;
}
*{box-sizing:border-box;margin:0;padding:0}
html,body{width:817px;height:1200px;overflow:hidden;background:var(--backdrop);font-family:"Poppins",sans-serif;color:var(--ink)}
.stage{position:absolute;left:0;top:0;width:1582px;height:2324px;transform:scale(.51643);transform-origin:0 0}
.screen{position:absolute;left:48px;width:1486px;background:var(--canvas);overflow:hidden}
.screen--home{top:45px;height:1063px}
.screen--overview{top:1157px;height:1104px}
.sidebar{position:absolute;left:0;top:0;width:292px;height:100%;background:var(--sidebar);color:#fff}
.brand{position:absolute;left:14px;top:30px;display:flex;align-items:center;gap:12px;font-size:25px;font-weight:500;letter-spacing:-.5px}
.brand-dot{width:38px;height:38px;border-radius:50%;background:var(--orange)}
.nav-item{position:absolute;left:22px;display:flex;align-items:center;gap:10px;font-size:17px;transform:translateY(-50%)}
.nav-item svg{width:18px;height:18px;fill:#fff}
.nav-heading{position:absolute;left:22px;right:60px;font-size:19px;transform:translateY(-50%);display:flex;justify-content:space-between}
.nav-heading svg{width:14px;height:14px;fill:#fff;margin-top:6px;margin-right:-40px}
.nav-band{position:absolute;left:0;width:292px;height:47px;background:var(--sidebar-band);display:flex;align-items:center;padding-left:22px;gap:10px;color:var(--orange);font-size:18px;font-weight:500}
.nav-band svg{width:24px;height:22px;fill:none;stroke:var(--orange);stroke-width:2.4}
.nav-band .chev{width:14px;height:14px;margin-left:auto;margin-right:12px;stroke-width:2}
.nav-band--active{background:var(--sidebar-active);font-weight:400}
.nav-band--active svg{fill:var(--orange);stroke:none;width:18px;height:18px}
.nav-band--page{background:var(--sidebar-active);font-weight:400;font-size:17px}
.nav-band--page svg{width:18px;height:18px;stroke-width:1.6}
.header{position:absolute;left:292px;right:0;top:0;height:71px;background:var(--orange);color:#fff}
.header-title{position:absolute;left:42px;top:50%;transform:translateY(-50%);font-size:28px;font-weight:600}
.header-crumb{position:absolute;left:42px;top:13px;font-size:14px}
.header-sub{position:absolute;left:42px;top:30px;font-size:22px;font-weight:600}
.header-user{position:absolute;right:42px;top:22px;width:26px;height:26px;fill:none;stroke:#fff;stroke-width:2}
.label{position:absolute;left:336px;font-size:19px;transform:translateY(-50%)}
.card{position:absolute;background:var(--card);border:1px solid var(--line);border-radius:0 0 0 22px;box-shadow:0 4px 10px rgba(0,0,0,.06)}
.card--orange{background:var(--orange);border-color:var(--orange);color:#fff}
.ico{fill:none;stroke:var(--orange);stroke-width:1.6}
.ico-dark{fill:none;stroke:#222;stroke-width:1.6}
.ico-white{fill:none;stroke:#fff;stroke-width:1.6}
.abs{position:absolute}
.title-22{font-size:22px;font-weight:600}
.body-16{font-size:16px}
.btn{position:absolute;background:var(--orange);color:#fff;font-size:15px;display:flex;align-items:center;justify-content:center;gap:8px}
.btn svg{width:12px;height:12px;fill:#fff}
.camp-card{text-align:center}
.gear-disc{position:absolute;left:50%;top:105px;width:114px;height:114px;margin-left:-57px;border-radius:50%;background:#fff;box-shadow:0 4px 14px rgba(0,0,0,.12);display:flex;align-items:center;justify-content:center}
.gear-disc svg{width:62px;height:62px}
.camp-count{position:absolute;left:52px;top:248px;font-size:44px;color:var(--orange);font-weight:400}
.camp-meta{position:absolute;left:92px;top:250px;text-align:left;font-size:14px;line-height:1.4}
.camp-meta b{font-weight:500;font-size:16px}
.camp-since{position:absolute;left:64px;top:310px;font-size:13px}
</style>
</head>
<body>
<svg width="0" height="0" style="position:absolute" aria-hidden="true">
  <symbol id="i-home" viewBox="0 0 20 20"><path d="M10 2 1 10h3v8h4v-5h4v5h4v-8h3z"/></symbol>
  <symbol id="i-bell" viewBox="0 0 20 20"><path d="M10 2a5 5 0 0 0-5 5v5l-2 3h14l-2-3V7a5 5 0 0 0-5-5zm-2 14a2 2 0 0 0 4 0z"/></symbol>
  <symbol id="i-gear" viewBox="0 0 20 20"><path d="M8.6 1h2.8l.5 2.6 1.6.7 2.2-1.5 2 2-1.5 2.2.7 1.6 2.6.5v2.8l-2.6.5-.7 1.6 1.5 2.2-2 2-2.2-1.5-1.6.7-.5 2.6H8.6l-.5-2.6-1.6-.7-2.2 1.5-2-2 1.5-2.2-.7-1.6L1 11.4V8.6l2.6-.5.7-1.6-1.5-2.2 2-2 2.2 1.5 1.6-.7zM10 7a3 3 0 1 0 0 6 3 3 0 0 0 0-6z"/></symbol>
  <symbol id="i-cogs" viewBox="0 0 20 20"><circle cx="7" cy="11" r="5"/><circle cx="15" cy="5" r="3.5"/><circle cx="7" cy="11" r="2" fill="#120d0b"/><circle cx="15" cy="5" r="1.3" fill="#120d0b"/></symbol>
  <symbol id="i-doc" viewBox="0 0 20 20"><path d="M4 1h8l4 4v14H4z" fill="none" stroke="currentColor" stroke-width="1.6"/><path d="M7 8h6M7 11h6M7 14h6" stroke="currentColor" stroke-width="1.4"/></symbol>
  <symbol id="i-file" viewBox="0 0 20 20"><path d="M4 1h8l4 4v14H4z" fill="none" stroke="currentColor" stroke-width="1.6"/></symbol>
  <symbol id="i-stack" viewBox="0 0 24 22"><rect x="1" y="8" width="12" height="12"/><rect x="10" y="2" width="12" height="12"/></symbol>
  <symbol id="i-chev" viewBox="0 0 14 14"><path d="M3 5l4 4 4-4"/></symbol>
  <symbol id="i-plus" viewBox="0 0 14 14"><path d="M5 0h4v5h5v4H9v5H5V9H0V5h5z"/></symbol>
  <symbol id="i-user" viewBox="0 0 26 26"><circle cx="13" cy="13" r="12"/><circle cx="13" cy="10" r="4.5"/><path d="M5 21c2-4 14-4 16 0"/></symbol>
  <symbol id="i-chart" viewBox="0 0 56 56"><path d="M4 52h50M8 52V38h7v14M20 52V32h7v20M32 52V26h7v26M44 52V18h7v34M6 30l14-10 10 6L48 6M40 6h8v8"/></symbol>
  <symbol id="i-check" viewBox="0 0 30 30"><path d="M26 13a12 12 0 1 1-5-9"/><path d="M9 14l5 5L27 5"/></symbol>
  <symbol id="i-pages" viewBox="0 0 30 34"><path d="M4 5h18v28H4z"/><path d="M8 1h18v28"/><path d="M8 11h10M8 15h10M8 19h10M8 23h10M8 27h10"/></symbol>
  <symbol id="i-stats" viewBox="0 0 50 50"><rect x="3" y="3" width="36" height="30"/><path d="M3 9h36M9 26v-6M15 26v-10M21 26v-4"/><circle cx="30" cy="30" r="9"/><path d="M36 37l9 9"/></symbol>
  <symbol id="i-cog-lg" viewBox="0 0 64 64"><path d="M24 20l2-5h6l2 5 5 2 5-2 4 4-2 5 2 5 5 2v6l-5 2-2 5 2 5-4 4-5-2-5 2-2 5h-6l-2-5-5-2-5 2-4-4 2-5-2-5-5-2v-6l5-2 2-5-2-5 4-4 5 2z"/><circle cx="29" cy="38" r="7"/><circle cx="46" cy="16" r="9"/><circle cx="46" cy="16" r="3.5"/></symbol>
  <symbol id="i-network" viewBox="0 0 50 50"><circle cx="12" cy="12" r="7"/><circle cx="38" cy="12" r="7"/><circle cx="12" cy="38" r="7"/><circle cx="38" cy="38" r="7"/><circle cx="25" cy="25" r="6"/><path d="M17 17l4 4M33 17l-4 4M17 33l4-4M33 33l-4-4"/></symbol>
  <symbol id="i-warn" viewBox="0 0 40 36"><path d="M20 3 2 33h36z"/><path d="M20 13v10M20 27v2"/></symbol>
</svg>

<div class="stage">

  <!-- Home screen -->
  <section class="screen screen--home">
    <aside class="sidebar">
      <div class="brand"><span class="brand-dot"></span>PlumVesta</div>
      <div class="nav-band nav-band--active" style="top:127px"><svg><use href="#i-home"/></svg>Home</div>
      <div class="nav-item" style="top:209px"><svg><use href="#i-bell"/></svg>All alerts</div>
      <div class="nav-item" style="top:252px"><svg><use href="#i-gear"/></svg>Manage</div>
      <div class="nav-heading" style="top:299px">Campaigns<svg><use href="#i-plus"/></svg></div>
      <div class="nav-band" style="top:345px"><svg><use href="#i-stack"/></svg>My custom campaign<svg class="chev"><use href="#i-chev"/></svg></div>
      <div class="nav-item" style="top:428px;color:#fff"><svg style="color:#fff"><use href="#i-doc"/></svg>Overview</div>
      <div class="nav-item" style="top:469px"><svg style="color:#fff"><use href="#i-file"/></svg>Files &amp; PlumTokens</div>
      <div class="nav-item" style="top:512px"><svg><use href="#i-cogs"/></svg>Resources</div>
      <div class="nav-item" style="top:554px"><svg><use href="#i-bell"/></svg>Alerts</div>
      <div class="nav-item" style="top:593px"><svg><use href="#i-gear"/></svg>Settings</div>
      <div class="nav-band" style="top:638px"><svg><use href="#i-stack"/></svg>My custom campaign<svg class="chev"><use href="#i-chev"/></svg></div>
    </aside>
    <header class="header">
      <div class="header-title">Home</div>
      <svg class="header-user"><use href="#i-user"/></svg>
    </header>

    <div class="label" style="top:121px">Teamspace</div>
    <div class="card" style="left:338px;top:152px;width:1102px;height:90px">
      <div class="abs title-22" style="left:30px;top:14px">Default</div>
      <div class="abs body-16" style="left:30px;top:50px">The default client is created as a part of your user account.</div>
    </div>

    <div class="label" style="top:296px">Subscription overview</div>
    <div class="card" style="left:338px;top:328px;width:486px;height:192px">
      <svg class="abs ico" style="left:28px;top:22px;width:56px;height:56px"><use href="#i-chart"/></svg>
      <div class="abs title-22" style="left:30px;top:94px">Starter pack usage</div>
      <div class="abs body-16" style="left:30px;top:132px">0 files active out of 10 allowed</div>
    </div>

    <div class="label" style="left:860px;top:296px">Files &amp; PlumTokens</div>
    <div class="card" style="left:862px;top:328px;width:486px;height:192px">
      <svg class="abs ico" style="left:34px;top:28px;width:46px;height:46px"><use href="#i-stats"/></svg>
      <div class="abs title-22" style="left:30px;top:94px">Statistics</div>
      <svg class="abs ico-dark" style="left:32px;top:138px;width:28px;height:28px"><use href="#i-check"/></svg>
      <div class="abs title-22" style="left:74px;top:136px">0</div>
      <svg class="abs ico-dark" style="left:326px;top:134px;width:28px;height:32px"><use href="#i-pages"/></svg>
      <div class="abs title-22" style="left:366px;top:136px">30</div>
    </div>

    <div class="label" style="top:603px">Campaigns</div>
    <div class="btn" style="left:1179px;top:578px;width:169px;height:40px">New Campaigns<svg><use href="#i-plus"/></svg></div>

    <div class="card camp-card" style="left:338px;top:635px;width:401px;height:354px">
      <div class="abs title-22" style="left:0;right:0;top:30px">My custom campaign</div>
      <div class="abs body-16" style="left:0;right:0;top:70px">This is my custom campaign for finding i</div>
      <div class="gear-disc"><svg class="ico"><use href="#i-cog-lg"/></svg></div>
      <div class="camp-count">0</div>
      <div class="camp-meta">Active<br><b>Files and PlumTokens</b></div>
      <div class="camp-since">Active since: Jul 25 2023 13:12</div>
    </div>
    <div class="card camp-card" style="left:767px;top:635px;width:401px;height:354px">
      <div class="abs title-22" style="left:0;right:0;top:30px">Default campaign</div>
      <div class="abs body-16" style="left:0;right:0;top:70px">Define your own mission, or combine differen...</div>
      <div class="gear-disc"><svg class="ico"><use href="#i-cog-lg"/></svg></div>
      <div class="camp-count">0</div>
      <div class="camp-meta">Active<br><b>Files and PlumTokens</b></div>
      <div class="camp-since">Active since: Jul 20 2023 12:17</div>
    </div>
  </section>

  <!-- Campaign overview screen -->
  <section class="screen screen--overview">
    <aside class="sidebar">
      <div class="brand"><span class="brand-dot"></span>PlumVesta</div>
      <div class="nav-item" style="top:142px"><svg><use href="#i-home"/></svg>Home</div>
      <div class="nav-item" style="top:184px"><svg><use href="#i-bell"/></svg>All alerts</div>
      <div class="nav-item" style="top:226px"><svg><use href="#i-gear"/></svg>Manage</div>
      <div class="nav-heading" style="top:298px">Campaigns<svg><use href="#i-plus"/></svg></div>
      <div class="nav-band" style="top:345px"><svg><use href="#i-stack"/></svg>My custom campaign<svg class="chev"><use href="#i-chev"/></svg></div>
      <div class="nav-band nav-band--page" style="top:410px"><svg style="color:var(--orange)"><use href="#i-doc"/></svg>Overview</div>
      <div class="nav-item" style="top:481px"><svg style="color:#fff"><use href="#i-file"/></svg>Files &amp; PlumTokens</div>
      <div class="nav-item" style="top:523px"><svg><use href="#i-cogs"/></svg>Resources</div>
      <div class="nav-item" style="top:565px"><svg><use href="#i-bell"/></svg>Alerts</div>
      <div class="nav-item" style="top:605px"><svg><use href="#i-gear"/></svg>Settings</div>
      <div class="nav-band" style="top:651px"><svg><use href="#i-stack"/></svg>My custom campaign<svg class="chev"><use href="#i-chev"/></svg></div>
    </aside>
    <header class="header">
      <div class="header-crumb">My custom campaign</div>
      <div class="header-sub">Overview</div>
      <svg class="header-user"><use href="#i-user"/></svg>
    </header>

    <div class="label" style="top:120px">Campaign</div>
    <div class="card card--orange" style="left:338px;top:152px;width:1102px;height:88px">
      <div class="abs" style="left:28px;top:8px;width:72px;height:72px;border-radius:50%;background:#fff;display:flex;align-items:center;justify-content:center"><svg class="ico" style="width:40px;height:40px"><use href="#i-cog-lg"/></svg></div>
      <div class="abs title-22" style="left:119px;top:14px">My custom campaign</div>
      <div class="abs body-16" style="left:120px;top:50px">This is my custom campaign for finding i</div>
    </div>

    <div class="label" style="top:296px">Campaign organisation</div>
    <div class="card" style="left:338px;top:328px;width:1106px;height:191px">
      <svg class="abs ico" style="left:30px;top:22px;width:56px;height:56px"><use href="#i-chart"/></svg>
      <div class="abs" style="left:112px;top:26px;font-size:16px;font-weight:600">Self-enabling Deliverables Proprietary Limited</div>
      <div class="abs body-16" style="left:112px;top:57px">Standard</div>
      <svg class="abs ico-dark" style="left:243px;top:106px;width:46px;height:46px"><use href="#i-network"/></svg>
      <div class="abs" style="left:313px;top:110px;font-size:27px;font-weight:500">86</div>
      <div class="abs" style="left:704px;top:26px;font-size:16px;font-weight:600">Unleash bleeding-edge mindshare</div>
      <div class="abs body-16" style="left:704px;top:57px">8 hours ago</div>
      <svg class="abs ico-dark" style="left:835px;top:106px;width:46px;height:46px"><use href="#i-network"/></svg>
      <div class="abs" style="left:905px;top:110px;font-size:27px;font-weight:500">8</div>
    </div>

    <div class="label" style="top:575px">Campaigns</div>
    <div class="card card--orange" style="left:338px;top:608px;width:525px;height:207px">
      <svg class="abs ico-white" style="left:24px;top:34px;width:36px;height:42px"><use href="#i-pages"/></svg>
      <div class="abs" style="left:68px;top:40px;font-size:21px;font-weight:500">Statistics</div>
      <svg class="abs ico-white" style="left:182px;top:118px;width:30px;height:30px"><use href="#i-check"/></svg>
      <div class="abs" style="left:226px;top:118px;font-size:21px">0</div>
      <svg class="abs ico-white" style="left:310px;top:114px;width:32px;height:38px"><use href="#i-pages"/></svg>
      <div class="abs" style="left:354px;top:118px;font-size:21px">30</div>
    </div>
    <div class="card card--orange" style="left:896px;top:608px;width:525px;height:207px">
      <svg class="abs ico-white" style="left:24px;top:34px;width:36px;height:42px"><use href="#i-pages"/></svg>
      <div class="abs" style="left:68px;top:38px;right:60px;font-size:21px;font-weight:500;line-height:1.45">Generate a collection of fictional organisations, Custom templates, Uploaded files and logos.</div>
    </div>

    <div class="label" style="top:879px">Alerts</div>
    <div class="card" style="left:338px;top:911px;width:533px;height:111px">
      <svg class="abs ico" style="left:22px;top:28px;width:40px;height:36px"><use href="#i-warn"/></svg>
      <div class="abs body-16" style="left:76px;top:32px">Alert statistics will appear here</div>
    </div>
  </section>

</div>
</body>
</html>
```